Business card for Luxury Portable Restroom Trailer company

We are a Luxury Portable Restroom Trailer Company Called FALCRIDGE HIRES. Based in Orange County California. We provide portable restroom trailers for events, such as, Weddings, Concerts, Charity events, Sporting events, Tournaments, Corporate events, ect. We rent and Sell the Luxury restrooms. Our colors are white, grey, and Orange. As you will see in the logo we uploaded.
There are 2 people in the company so the names and titles will change for the 3 people but card will remain the same. Here is the information for each Person: Dwight Penner CFO 555 318-0476
next Person: Leon Marchetti VP 555 318-0476
Next Person: Owen Marchetti CEO 555 318-0476
Information to include on the card: Luxury Restroom Trailers Rental and Sales. Weddings, Concerts, Charity, Sporting and Corp. Events.

```html
<!DOCTYPE html>
<html lang="en">
<head>
<meta charset="utf-8">
<title>Falcridge Hires – Business Card</title>
<link rel="stylesheet" href="https://fonts.googleapis.com/css2?family=Montserrat:wght@400;500;800;900&display=swap">
<style>
  :root {
    --orange: #f07230;
    --grey: #5d5e60;
    --ink: #222222;
    --card: #ffffff;
    --stage: #e6e6e6;
  }
  * { margin: 0; padding: 0; box-sizing: border-box; }
  html, body { width: 1200px; height: 960px; overflow: hidden; }
  body {
    background: var(--stage);
    font-family: "Montserrat", sans-serif;
    position: relative;
  }
  .card {
    position: absolute;
    left: 250px;
    width: 700px;
    height: 400px;
    background: var(--card);
    border-radius: 22px;
    box-shadow: 0 6px 18px rgba(0,0,0,0.18);
    overflow: hidden;
  }
  .card--front { top: 60px; }
  .card--back { top: 500px; }

  /* Front */
  .brand-block {
    position: absolute;
    top: 88px; left: 0; right: 0;
    text-align: center;
  }
  .brand-name {
    font-weight: 900;
    font-size: 62px;
    letter-spacing: 2px;
    color: var(--grey);
    line-height: 1;
  }
  .services {
    position: absolute;
    top: 250px; left: 0; right: 0;
    text-align: center;
    font-weight: 500;
    font-size: 19px;
    color: var(--ink);
    line-height: 1.7;
  }
  .services .dot {
    display: inline-block;
    width: 10px; height: 10px;
    border-radius: 50%;
    background: var(--orange);
    margin: 0 8px 2px 10px;
    vertical-align: middle;
  }

  /* Back */
  .mark-area {
    position: absolute;
    left: 40px; top: 60px;
    width: 300px; height: 280px;
    display: flex; flex-direction: column;
    align-items: center; justify-content: center;
    gap: 22px;
  }
  .mark-ring {
    width: 150px; height: 150px;
    border-radius: 50%;
    border: 12px solid var(--orange);
  }
  .mark-name {
    font-weight: 900;
    font-size: 26px;
    letter-spacing: 1px;
    color: var(--orange);
  }
  .divider {
    position: absolute;
    left: 372px; top: 70px;
    width: 2px; height: 260px;
    background: var(--orange);
  }
  .team {
    position: absolute;
    left: 400px; top: 62px;
    list-style: none;
  }
  .member { margin-bottom: 16px; }
  .member-name {
    font-weight: 800;
    font-size: 22px;
    text-transform: uppercase;
    color: var(--grey);
    line-height: 1.1;
  }
  .member-name .surname { color: var(--orange); }
  .member-title {
    font-size: 16px;
    color: var(--ink);
    margin: 3px 0 2px 14px;
  }
  .member-phone {
    font-size: 16px;
    color: var(--ink);
    margin-left: 14px;
    display: flex; align-items: center; gap: 8px;
  }
  .member-phone svg { width: 16px; height: 16px; fill: var(--orange); }
</style>
</head>
<body>

<section class="card card--front">
  <div class="brand-block">
    <div class="brand-name">FALCRIDGE HIRES</div>
  </div>
  <div class="services">
    <p><span class="dot"></span>Luxury Restroom Trailers Rental and Sales</p>
    <p><span class="dot"></span>Weddings <span class="dot"></span>Concerts <span class="dot"></span>Charity <span class="dot"></span>Sporting and Corp <span class="dot"></span>Events</p>
  </div>
</section>

<section class="card card--back">
  <div class="mark-area">
    <div class="mark-ring"></div>
    <div class="mark-name">FALCRIDGE HIRES</div>
  </div>
  <div class="divider"></div>
  <ul class="team">
    <li class="member">
      <div class="member-name">Dwight <span class="surname">Penner</span></div>
      <div class="member-title">CFO</div>
      <div class="member-phone"><svg viewBox="0 0 24 24"><path d="M6.6 10.8a15.1 15.1 0 0 0 6.6 6.6l2.2-2.2a1 1 0 0 1 1-.25 11.4 11.4 0 0 0 3.6.57 1 1 0 0 1 1 1V20a1 1 0 0 1-1 1A17 17 0 0 1 3 4a1 1 0 0 1 1-1h3.5a1 1 0 0 1 1 1c0 1.25.2 2.45.57 3.57a1 1 0 0 1-.25 1z"/></svg>555 318-0476</div>
    </li>
    <li class="member">
      <div class="member-name">Leon <span class="surname">Marchetti</span></div>
      <div class="member-title">VP</div>
      <div class="member-phone"><svg viewBox="0 0 24 24"><path d="M6.6 10.8a15.1 15.1 0 0 0 6.6 6.6l2.2-2.2a1 1 0 0 1 1-.25 11.4 11.4 0 0 0 3.6.57 1 1 0 0 1 1 1V20a1 1 0 0 1-1 1A17 17 0 0 1 3 4a1 1 0 0 1 1-1h3.5a1 1 0 0 1 1 1c0 1.25.2 2.45.57 3.57a1 1 0 0 1-.25 1z"/></svg>555 318-0476</div>
    </li>
    <li class="member">
      <div class="member-name">Owen <span class="surname">Marchetti</span></div>
      <div class="member-title">CEO</div>
      <div class="member-phone"><svg viewBox="0 0 24 24"><path d="M6.6 10.8a15.1 15.1 0 0 0 6.6 6.6l2.2-2.2a1 1 0 0 1 1-.25 11.4 11.4 0 0 0 3.6.57 1 1 0 0 1 1 1V20a1 1 0 0 1-1 1A17 17 0 0 1 3 4a1 1 0 0 1 1-1h3.5a1 1 0 0 1 1 1c0 1.25.2 2.45.57 3.57a1 1 0 0 1-.25 1z"/></svg>555 318-0476</div>
    </li>
  </ul>
</section>

</body>
</html>
```